HearthMile business card and stationary design

We are looking for a simple yet elegant design for our mortgage company business card and stationary.

The card should include:
Name (Marcus Pell)
Title (CEO)
Phone Number (555-555-0182)
Address (48 Birchwell Court, Suite 314, Wrenmoor, NX 00314)
Email (email@hearthmile.example)
"NMLS" i.e. (NMLS 61947)
"Company NMLS" (Company NMLS 274615)

Contact Information for Business Card

See above

```html
<!DOCTYPE html>
<html lang="en">
<head>
<meta charset="utf-8">
<title>HearthMile Business Card</title>
<link rel="stylesheet" href="https://fonts.googleapis.com/css2?family=Source+Sans+3:wght@400;600;700&display=swap">
<style>
  :root {
    --navy: #1a2330;
    --blue: #1ea0db;
    --card-light: #f4f4f4;
    --backdrop: #e4e4e4;
    --ink: #1f2a36;
    --white: #ffffff;
  }
  * { margin: 0; padding: 0; box-sizing: border-box; }
  html, body {
    width: 1200px; height: 960px; overflow: hidden;
    background: var(--backdrop);
    font-family: "Source Sans 3", Arial, sans-serif;
  }
  .canvas { position: relative; width: 1200px; height: 960px; }

  .card { position: absolute; left: 305px; width: 593px; height: 339px; overflow: hidden; }
  .card-front { top: 119px; background: var(--navy); }
  .card-back { top: 510px; background: var(--card-light); }

  .wordmark {
    position: absolute; display: flex; align-items: center;
    font-weight: 600; letter-spacing: -0.5px; line-height: 1;
  }
  .wordmark-mark { display: block; background: var(--blue); }
  .card-front .wordmark {
    left: 0; right: 0; top: 140px; justify-content: center; gap: 18px;
    font-size: 72px; color: var(--white);
  }
  .card-front .wordmark-mark { width: 22px; height: 22px; }
  .card-back .wordmark {
    left: 45px; top: 62px; gap: 12px;
    font-size: 46px; color: var(--ink);
  }
  .card-back .wordmark-mark { width: 14px; height: 14px; }

  .accent-tab { position: absolute; left: 0; top: 181px; width: 16px; height: 36px; background: var(--blue); }

  .person { position: absolute; left: 45px; top: 178px; }
  .person-name { font-size: 20px; font-weight: 700; color: var(--blue); letter-spacing: 0.3px; line-height: 24px; }
  .person-title { font-size: 15px; color: var(--ink); line-height: 20px; }
  .person-rule { width: 34px; height: 2px; background: var(--ink); margin-top: 22px; }
  .person-nmls { margin-top: 26px; font-size: 15px; color: var(--ink); }
  .person-nmls .label { color: var(--blue); }

  .contact { position: absolute; left: 359px; top: 182px; font-size: 15px; color: var(--ink); line-height: 20px; }
  .contact-address { margin-bottom: 11px; }
  .contact-line { display: flex; align-items: center; gap: 5px; }
  .contact-line svg { width: 13px; height: 13px; flex: none; }

  .footer-bands { position: absolute; left: 0; bottom: 0; width: 593px; height: 31px; }
  .company-nmls {
    position: absolute; right: 37px; bottom: 7px;
    font-size: 16px; letter-spacing: 0.2px; color: var(--white);
  }
</style>
</head>
<body>
<main class="canvas">

  <section class="card card-front" aria-label="Card front">
    <div class="wordmark"><span class="wordmark-mark"></span>HearthMile</div>
  </section>

  <section class="card card-back" aria-label="Card back">
    <div class="wordmark"><span class="wordmark-mark"></span>HearthMile</div>

    <span class="accent-tab"></span>
    <div class="person">
      <p class="person-name">MARCUS PELL</p>
      <p class="person-title">CEO</p>
      <div class="person-rule"></div>
      <p class="person-nmls"><span class="label">NMLS</span> 61947</p>
    </div>

    <div class="contact">
      <p class="contact-address">48 Birchwell Court, Suite 314<br>Wrenmoor, NX 00314</p>
      <p class="contact-line">
        <svg viewBox="0 0 16 16" aria-hidden="true"><path fill="#1ea0db" d="M3.6 1.5l2.3 2.8-1.3 1.8c.9 2 2.4 3.5 4.4 4.4l1.8-1.3 2.8 2.3-1.4 2.2C7 13.5 2.5 9 1.4 2.9z"/></svg>
        555-555-0182
      </p>
      <p class="contact-line">
        <svg viewBox="0 0 16 16" aria-hidden="true"><rect x="1.5" y="3.5" width="13" height="9" fill="none" stroke="#1ea0db" stroke-width="1.6"/><path d="M1.5 3.5l6.5 5 6.5-5" fill="none" stroke="#1ea0db" stroke-width="1.6"/></svg>
        email@hearthmile.example
      </p>
      <p class="contact-line">
        <svg viewBox="0 0 16 16" aria-hidden="true"><g fill="none" stroke="#1ea0db" stroke-width="1.4"><circle cx="8" cy="8" r="6.3"/><ellipse cx="8" cy="8" rx="2.8" ry="6.3"/><path d="M1.7 8h12.6"/></g></svg>
        www.hearthmile.example
      </p>
    </div>

    <svg class="footer-bands" viewBox="0 0 593 31" aria-hidden="true">
      <polygon points="0,16 352,16 345,31 0,31" fill="#1a2330"/>
      <polygon points="364,0 593,0 593,31 345,31" fill="#1ea0db"/>
    </svg>
    <p class="company-nmls">Company NMLS 274615</p>
  </section>

</main>
</body>
</html>
```